Business card design needed to incorporate existing logo

We need a business card for a new modern Accounting & Business Solutions company call TelmaNord Partners.com.au servicing all of Australia.
My tagline is Steady Ledger Answers... that deliver.

We specialise in Cloud Accounting and this is our primary focus. We also provide tax representation, debt recovery, computer, tablet and smart phone sales.

I would like a design that uses my corporate, trustworthy colours of blue/white, black/grey however am open to suggestion. I have attached my logo to go on the card somewhere,of which you will see the colour scheme.

I am after a card that STANDS OUT, somewhere between it not being too busy and not being a baron waste of space.

A 'cloud' incorporated in the design may work well, up to your artistic judgement. I know what I like when I see it; it is harder to put into words!

Excited to see your ideas!
I have added my logo predominately (blue/white) and for additional opportunity have added my reverse logo (darker one). I have used the blue/white on my website and letterhead. I will be using both on my vehicle signage.

Target Market(s)

Tradesmen and small-medium businesses of all descriptions Australia-wide

Industry/Entity Type

Debt

Contact Information for Business Card

Doug Hallett
Principal (optional)
TelmaNord Partners.com.au
Steady Ledger Answers... that deliver

P: 1800 493 518
M: 0412 658 071 (optional)
W: www.telmanordpartners.com.au
E: admin@telmanordpartners.com.au

Logo Text

Steady Ledger Answers... that deliver!

Logo styles of interest
Wordmark Logo
Requirements
Must have
• Must look professional and of high quality not cheap.

My logo and my tagline 'Steady Ledger Answers... that deliver'.

I have my colourscheme in mind as per my attached logo, however am open to suggestion. I want to see what you can create that I would not have thought of.

Modern, innovative.
Something I won't look at and think, 'I could have done that myself'.

Must be able to be printed on Prinvo 300gm premium cards and the artwork provided to me.
Nice to have
• Title of Principal is optional depending on space and judement call of look/fee.
M: (mobile) number is also optional as above.

Somthing cloud related given the Cloud Accounting aspect may be relevant. I leave it to your artistic design and judgement.
Should not have
• Must not look cheap.

```html
<!DOCTYPE html>
<html lang="en">
<head>
<meta charset="utf-8">
<title>TelmaNord Partners – Business Card</title>
<link rel="stylesheet" href="https://fonts.googleapis.com/css2?family=Open+Sans:wght@300;400;700;800&display=swap">
<style>
  :root {
    --navy: #1f2a5a;
    --navy-soft: #2a3670;
    --brand-blue: #2f6fb0;
    --brand-light: #6fa4dc;
    --white: #ffffff;
    --backdrop: #d6d6d8;
    --card-radius: 26px;
  }
  * { box-sizing: border-box; margin: 0; padding: 0; }
  html, body {
    width: 1200px; height: 985px; overflow: hidden;
    background: var(--backdrop);
    font-family: "Open Sans", Arial, sans-serif;
  }
  .canvas { position: relative; width: 1200px; height: 985px; }

  .card {
    position: absolute; left: 220px;
    width: 760px; height: 430px;
    border-radius: var(--card-radius);
    overflow: hidden;
    box-shadow: 0 10px 24px rgba(0,0,0,.18);
  }

  /* Back of card */
  .card-back { top: 45px; background: var(--navy); }
  .card-back .glow {
    position: absolute; left: -40px; top: -30px; width: 380px; height: 380px;
    border-radius: 50%;
    background: radial-gradient(circle at 50% 50%, rgba(255,255,255,.09), rgba(255,255,255,0) 70%);
  }
  .card-back .brand {
    position: absolute; left: 0; right: 0; top: 150px; text-align: center;
  }
  .wordmark { font-weight: 300; letter-spacing: 3px; white-space: nowrap; }
  .card-back .wordmark { color: var(--brand-light); font-size: 44px; }
  .brand-dot {
    display: inline-block; width: 26px; height: 26px; border-radius: 50%;
    background: var(--brand-light); vertical-align: middle; margin-left: 12px; position: relative; top: -4px;
  }
  .card-back .web {
    margin-top: 28px; color: var(--white); font-size: 22px; letter-spacing: 1.5px;
  }
  .card-back .web strong { font-weight: 700; }

  /* Front of card */
  .card-front { top: 510px; background: var(--white); }
  .card-front .brand {
    position: absolute; left: 0; width: 312px; top: 150px;
    display: flex; align-items: center; justify-content: center; gap: 12px;
  }
  .card-front .wordmark {
    color: var(--brand-blue); font-size: 36px; line-height: 1.1; letter-spacing: 2px;
  }
  .card-front .wordmark span { display: block; }
  .card-front .brand-dot { background: var(--brand-blue); width: 22px; height: 22px; margin-left: 0; top: 0; }

  .divider { position: absolute; top: 0; left: 0; width: 760px; height: 430px; }
  .info {
    position: absolute; left: 378px; top: 40px; width: 370px;
    color: var(--white);
  }
  .info .name { font-size: 30px; font-weight: 800; line-height: 1.15; }
  .info .title { font-size: 23px; font-weight: 700; margin-bottom: 18px; }
  .info .company { font-size: 17px; font-weight: 700; line-height: 1.3; margin-bottom: 18px; }
  .info .contacts { list-style: none; font-size: 16px; font-weight: 700; line-height: 1.55; }
</style>
</head>
<body>
<main class="canvas">

  <section class="card card-back" aria-label="Business card back">
    <div class="glow" role="img" aria-label="Soft light decorative glow"></div>
    <div class="brand">
      <div><span class="wordmark">TelmaNord Partners</span><span class="brand-dot"></span></div>
      <p class="web">www.<strong>telmanordpartners</strong>.com.au</p>
    </div>
  </section>

  <section class="card card-front" aria-label="Business card front">
    <svg class="divider" viewBox="0 0 760 430" aria-hidden="true">
      <polygon points="340,0 760,0 760,430 340,430" fill="var(--navy)"/>
      <polygon points="312,0 330,0 330,430 312,430" fill="var(--navy)"/>
      <polygon points="330,130 340,140 340,120" fill="var(--navy)"/>
      <circle cx="650" cy="330" r="140" fill="var(--navy-soft)" opacity=".45"/>
    </svg>

    <div class="brand">
      <span class="wordmark"><span>TelmaNord</span><span>Partners</span></span><span class="brand-dot"></span>
    </div>

    <div class="info">
      <h1 class="name">Doug Hallett</h1>
      <p class="title">Principal</p>
      <p class="company">TelmaNord Partners.com.au<br>Steady Ledger Answers</p>
      <ul class="contacts">
        <li>P: 1800 493 518</li>
        <li>M: 0412 658 071</li>
        <li>E: admin@telmanordpartners.com.au</li>
        <li>W: www.telmanordpartners.com.au</li>
      </ul>
    </div>
  </section>

</main>
</body>
</html>
```